real esate business card with company logo and name

we need a business card design for a real esate company

The company name is Walsh & Brand Pty Ltd, and we have our logo designed and will upload. We want classic or moden feel. Black or white background. looks more textured. Should include folowinginformations
Owen Walsh and Lucy Brand
Sales Agents & Onsite Manager
p: 07 5948 2063
F: 07 5948 2174
M:0431 857 219
3/42 Marlow Crescent, FERNLEA QLD 4213

We want this business card looks professonal. Thank you in advance.

Industry/Entity Type

Real Estate Agent

Contact Information for Business Card

Owen Walsh and Lucy Brand
Onsite Manager & Sales Agents
p: 07 5948 2063
M:0431 857 219

Font styles to use
Serif

Colors
000000
fbfbfb
333333
959595

Requirements
Must have
• company logo and name, black or white back ground

```html
<!DOCTYPE html>
<html lang="en">
<head>
<meta charset="utf-8">
<title>Walsh &amp; Brand Pty Ltd – Business Card</title>
<link href="https://fonts.googleapis.com/css2?family=Source+Sans+3:wght@400;600&display=swap" rel="stylesheet">
<style>
  :root {
    --ink-black: #000000;
    --paper-white: #fbfbfb;
    --charcoal: #333333;
    --charcoal-deep: #1e1e1e;
    --mid-grey: #959595;
    --stage: #e6e4e0;
  }
  * { box-sizing: border-box; margin: 0; padding: 0; }
  html, body { width: 1200px; height: 892px; overflow: hidden; }
  body {
    background: var(--stage);
    font-family: "Source Sans 3", "Myriad Pro", sans-serif;
    display: flex; align-items: center; justify-content: center;
  }
  .business-card {
    position: relative;
    width: 840px; height: 480px;
    display: flex;
    overflow: hidden;
    box-shadow: 0 10px 30px rgba(0,0,0,.25);
  }
  .brand-panel {
    position: relative;
    width: 330px; height: 100%;
    background: linear-gradient(135deg, #ffffff 0%, var(--paper-white) 55%, #ececec 100%);
    display: flex; flex-direction: column; align-items: center; justify-content: center;
    gap: 26px;
  }
  .edge-tab {
    position: absolute; left: 0; top: 38px; bottom: 38px; width: 26px;
    background: linear-gradient(90deg, #2a2a2a, var(--charcoal));
    border-radius: 0 10px 10px 0;
  }
  .brand-mark {
    width: 96px; height: 96px;
    background: var(--mid-grey);
  }
  .brand-name {
    color: var(--mid-grey);
    font-weight: 400; font-size: 22px; letter-spacing: 1px;
    text-transform: uppercase;
  }
  .contact-panel {
    flex: 1; height: 100%;
    background: linear-gradient(160deg, #3a3a3a 0%, var(--charcoal) 45%, var(--charcoal-deep) 100%);
    color: var(--paper-white);
    padding: 44px 40px 40px 36px;
    display: flex; flex-direction: column; justify-content: space-between;
  }
  .agent-names { font-size: 42px; font-weight: 400; line-height: 1.05; }
  .agent-role { font-size: 24px; margin-top: 10px; color: #e4e4e4; }
  .contact-list { list-style: none; display: flex; flex-direction: column; gap: 6px; }
  .contact-item { display: flex; align-items: flex-start; gap: 16px; font-size: 24px; line-height: 1.2; }
  .contact-icon {
    flex: none; width: 20px; height: 20px; margin-top: 4px;
    background: var(--paper-white); border-radius: 2px;
  }
  .address-lines { text-transform: none; }
</style>
</head>
<body>
  <article class="business-card">
    <section class="brand-panel">
      <span class="edge-tab"></span>
      <span class="brand-mark"></span>
      <p class="brand-name">Walsh &amp; Brand Pty Ltd</p>
    </section>
    <section class="contact-panel">
      <header>
        <h1 class="agent-names">Owen Walsh and Lucy Brand</h1>
        <p class="agent-role">Onsite Manager &amp; Sales Agents</p>
      </header>
      <ul class="contact-list">
        <li class="contact-item">
          <svg class="contact-icon" viewBox="0 0 20 20" aria-label="Phone">
            <path d="M6 4c1 0 1.6 2.4 1.6 3 0 .8-1.2 1-1 1.8.4 1.4 2 3 3.6 3.6.8.2 1-1 1.8-1 .6 0 3 .6 3 1.6 0 1-1.2 2.4-2.4 2.4C8 15.4 4.6 12 4.6 7.4 4.6 5.2 5 4 6 4z" fill="var(--charcoal)"/>
          </svg>
          <span>07 5948 2063</span>
        </li>
        <li class="contact-item">
          <svg class="contact-icon" viewBox="0 0 20 20" aria-label="Mobile">
            <rect x="6" y="3" width="8" height="14" rx="1.2" fill="none" stroke="var(--charcoal)" stroke-width="1.6"/>
            <rect x="8" y="5.5" width="4" height="7" fill="var(--charcoal)"/>
          </svg>
          <span>0431 857 219</span>
        </li>
        <li class="contact-item">
          <svg class="contact-icon" viewBox="0 0 20 20" aria-label="Address">
            <path d="M10 3.5 3.5 9.5h2v6.5h3.5v-4h2v4h3.5V9.5h2z" fill="var(--charcoal)"/>
          </svg>
          <span class="address-lines">3/42 Marlow Crescent,<br>FERNLEA QLD 4213</span>
        </li>
      </ul>
    </section>
  </article>
</body>
</html>
```